B2B Tear Sheet / Flyer for Corvath Summit Partners

Design multiple creative treatments for a 1-page, 2-sided tear sheet/flyer for a B2B consulting firm called Corvath Summit Partners, targeting Private Equity firms, Family Offices, Investment Banks, and Independent Sponsors. This piece will be handed out at conferences, 1-on-1 meetings, and potential snail mail (direct mail) campaigns. Eventually, the piece could also be made available on our website. The company is in start-up mode, so our website is not yet up and working. But we do have a logo and color palette.

```html
<!DOCTYPE html>
<html lang="en">
<head>
<meta charset="utf-8">
<title>Corvath Summit Partners – Fractional Marketing Services Tear Sheet</title>
<link href="https://fonts.googleapis.com/css2?family=Noto+Serif:ital,wght@0,400;0,700;1,400&family=Tinos:ital,wght@0,400;0,700;1,400;1,700&display=swap" rel="stylesheet">
<style>
:root{
  --green:#4b6b4d;
  --green-dark:#3f5f42;
  --ink:#4a4a4a;
  --rule:#9aa59a;
  --panel-gray:#7e8083;
  --navy:#114b7f;
  --blue:#1b72b0;
  --teal:#1e6d79;
  --footer-gray:#8b8c8e;
  --stage:#b4b4b4;
  --white:#ffffff;
}
*{box-sizing:border-box;margin:0;padding:0}
html,body{width:1200px;height:777px;overflow:hidden;background:var(--stage)}
body{position:relative;font-family:"Tinos",serif;color:var(--ink)}
.page{position:absolute;top:41px;width:537px;height:695px;background:var(--white);overflow:hidden}
.page--front{left:42px}
.page--back{left:620px}
.abs{position:absolute}
.heading{font-family:"Noto Serif",serif;font-weight:700;color:var(--green);line-height:1.05}
.rule{position:absolute;height:1px;background:var(--rule)}
b{color:#555;font-weight:700}

/* brand block */
.brand-area{left:0;top:0;width:242px;height:144px;background:linear-gradient(100deg,#fff 45%,#e4e5e5 100%)}
.brand-area--back{width:243px;height:94px}
.brand{position:absolute;left:0;right:0;text-align:center;font-family:"Noto Serif",serif;font-weight:400;color:var(--green)}
.brand-mark{display:block;margin:0 auto 6px;width:14px;height:14px;background:var(--green)}
.brand-name{font-size:21px;line-height:1.1}
.brand-sub{font-size:9px;letter-spacing:7px;margin-top:6px;padding-left:7px}

.photo{position:absolute}
.photo--markets{left:245px;top:0;width:256px;height:144px;background:linear-gradient(135deg,#0b3a5a 0%,#1f7fa8 45%,#4fb6d6 70%,#0d3c5c 100%)}
.accent-bar{position:absolute;left:504px;top:0;width:33px;height:144px;background:var(--green)}

/* sidebar */
.sidebar{left:0;top:144px;width:169px;height:506px;background:linear-gradient(180deg,#fff 0%,#eceded 60%,#dfe0e0 100%)}
.sidebar-title{position:absolute;left:48px;top:506px;transform-origin:0 0;transform:rotate(-90deg);white-space:nowrap;font-family:"Noto Serif",serif;font-weight:400;color:var(--green);font-size:33px;line-height:0.92;display:inline-block}
.sidebar-title span{display:block}
.sidebar-title .line-end{text-align:right}
.sidebar-tagline{position:absolute;left:118px;top:468px;transform-origin:0 0;transform:rotate(-90deg);white-space:nowrap;font-family:"Tinos",serif;font-style:italic;color:var(--green);font-size:15px}

.front-headline{left:181px;top:156px;width:350px;font-size:16px}
.front-intro{left:181px;top:214px;width:340px;font-size:7.8px;line-height:9.7px;text-align:justify}
.benefits-headline{left:182px;top:308px;width:340px;font-size:16px}

.benefit{position:absolute;left:182px;width:339px;height:39px}
.benefit-icon{position:absolute;left:0;top:0;width:60px;height:39px;border:1px solid var(--green);display:flex;align-items:center;justify-content:center}
.benefit-text{position:absolute;left:65px;top:0;width:274px;height:39px;border:1px solid var(--green);display:flex;align-items:center;padding-left:10px;font-size:11px;line-height:11.5px;color:#5a5a5a}
.benefit-text b{color:#5a5a5a}

/* footer */
.footer{position:absolute;top:649px;height:29px}
.footer-name{left:0;width:242px;background:var(--green);color:#fff;font-family:"Noto Serif",serif;font-size:12.5px;display:flex;align-items:center;padding-left:27px}
.footer-contacts{left:246px;width:291px;background:var(--footer-gray);color:#fff;font-size:6.2px;line-height:8px;display:flex;align-items:center}
.contact{display:flex;align-items:center;gap:4px;padding:0 6px;height:18px}
.contact + .contact{border-left:1px solid #d6d6d6}
.contact svg{flex:none}
.footer-copy{position:absolute;left:150px;top:6px;padding-left:12px;border-left:1px solid #cfd8cf;font-size:6.4px;line-height:8.5px}

/* back page */
.photo--ai{left:246px;top:0;width:291px;height:94px;background:linear-gradient(120deg,#0b2f4f 0%,#15689a 40%,#4cb2d8 65%,#0a3556 100%)}
.services-title{position:absolute;left:260px;top:30px;color:#fff;font-family:"Noto Serif",serif;font-weight:700;font-size:24px;line-height:26px}
.mission-band{left:0;top:98px;width:242px;height:35px;background:var(--green);color:#fff;font-family:"Noto Serif",serif;font-weight:700;font-size:16px;padding:8px 16px}
.mission-text{left:16px;top:143px;width:216px;font-size:7.1px;line-height:8.8px;text-align:justify}
.mission-contact{left:16px;top:256px;width:216px;font-size:7.1px;line-height:8.8px}
.founder-headline{left:16px;top:298px;font-size:16px}
.photo--founder{left:110px;top:303px;width:122px;height:79px;background:linear-gradient(135deg,#d9dde2 0%,#9fb1c6 50%,#e6e2dc 100%)}
.founder-text{left:16px;top:339px;width:216px;font-size:7.1px;line-height:8.8px;text-align:justify}
.founder-text--narrow{width:88px}
.founder-text--rest{top:392px}
.quote-headline{left:16px;top:478px;font-size:16px}
.proof-list{left:16px;top:535px;width:216px;font-size:6.9px;line-height:8.2px;list-style:none}
.proof-list li{position:relative;padding-left:16px;margin-bottom:2px;text-align:justify}
.proof-list li::before{content:"•";position:absolute;left:0}

.panel{position:absolute;color:#fff;padding:8px 10px 8px 12px}
.panel-title{font-family:"Noto Serif",serif;font-weight:700;font-size:12px;line-height:13.5px}
.panel-rule{height:1px;background:rgba(255,255,255,.75);margin:6px 0 8px}
.panel-note{font-size:7.3px;line-height:12px}
.panel-list{list-style:none;font-size:7.3px;line-height:8.5px}
.panel-list li{position:relative;padding-left:8px;margin-bottom:3.7px}
.panel-list li::before{content:"•";position:absolute;left:0}
.panel--retained{left:246px;top:98px;width:143px;height:287px;background:var(--panel-gray)}
.panel--audit{left:393px;top:98px;width:144px;height:287px;background:var(--navy)}
.panel--launch{left:246px;top:389px;width:291px;height:155px;background:var(--blue)}
.panel--special{left:246px;top:549px;width:291px;height:97px;background:var(--teal)}
.col-right{position:absolute;left:157px;width:128px}
</style>
</head>
<body>

<!-- FRONT -->
<section class="page page--front">
  <div class="abs brand-area">
    <div class="brand" style="top:48px">
      <span class="brand-mark"></span>
      <div class="brand-name">Corvath Summit</div>
      <div class="brand-sub">PARTNERS</div>
    </div>
  </div>
  <div class="photo photo--markets" role="img" aria-label="Businessman in a suit touching a glowing financial growth chart"></div>
  <div class="accent-bar"></div>

  <div class="abs sidebar"></div>
  <div class="sidebar-title"><span>Fractional Marketing</span><span class="line-end">Services</span></div>
  <div class="sidebar-tagline">The Alternative to a Full-Time Marketing Staff</div>

  <h1 class="abs heading front-headline">For Private Equity Funds, Family Offices &amp; Investment Banks</h1>
  <div class="rule" style="left:181px;top:203px;width:340px"></div>
  <p class="abs front-intro">Hiring a full-time marketing staff, or even a single marketing employee, can be an expensive proposition for a middle market firm. <b>Corvath Summit Partners</b> provides bespoke <b>Part-Time Marketing Services</b> to middle market clients, which allow them to receive best-in-class corporate marketing at a fraction of the cost of a full-time Analyst or Associate, or even an entry-level Marketing Coordinator. <b>Fractional Marketing Services</b> have been used for years for <b>Private Equity</b> portfolio companies, but only recently have they been made available to <b>Private Equity Funds</b> themselves, <b>Family Offices</b>, and <b>Investment Banks</b>.</p>
  <div class="rule" style="left:181px;top:294px;width:340px"></div>
  <h2 class="abs heading benefits-headline">Benefits of Using Corvath Summit Partners Fractional Marketing Services</h2>

  <div class="benefit" style="top:358px">
    <div class="benefit-icon"><svg width="24" height="24" viewBox="0 0 24 24" fill="none" stroke="#4b6b4d" stroke-width="1.2"><circle cx="12" cy="12" r="6"/><circle cx="12" cy="12" r="2.5"/><path d="M12 2v4M12 18v4M2 12h4M18 12h4M5 5l3 3M19 5l-3 3M5 19l3-3M19 19l-3-3"/></svg></div>
    <div class="benefit-text"><span><b>Best-in-Class Marketing</b> strategies, tactics &amp; execution for a fraction of the cost of an Analyst</span></div>
  </div>
  <div class="benefit" style="top:404px">
    <div class="benefit-icon"><svg width="30" height="24" viewBox="0 0 30 24" fill="none" stroke="#4b6b4d" stroke-width="1.2"><circle cx="15" cy="6" r="3"/><path d="M10 14c0-3 2-5 5-5s5 2 5 5"/><circle cx="6" cy="13" r="3.5"/><circle cx="24" cy="13" r="3.5"/><circle cx="15" cy="18" r="3.5"/><path d="M13.5 18l1 1 2-2"/></svg></div>
    <div class="benefit-text"><span>Leverage the experience of a 17+ year Private Equity Chief Marketing Officer</span></div>
  </div>
  <div class="benefit" style="top:451px">
    <div class="benefit-icon"><svg width="24" height="24" viewBox="0 0 24 24" fill="none" stroke="#4b6b4d" stroke-width="1.2"><path d="M3 10v11h18V10"/><path d="M12 12v9M3 10c3 0 6 1 9 2 3-1 6-2 9-2"/><circle cx="12" cy="6" r="3"/><path d="M12 1v1M8 3l1 1M16 3l-1 1"/></svg></div>
    <div class="benefit-text"><span>No need to stay knowledgeable on dynamically changing marketing and lead generation tactics and tools</span></div>
  </div>
  <div class="benefit" style="top:497px">
    <div class="benefit-icon"><svg width="24" height="24" viewBox="0 0 24 24" fill="none" stroke="#4b6b4d" stroke-width="1.2"><circle cx="12" cy="12" r="9.5"/><path d="M9 15l6-6"/><circle cx="9.5" cy="9.5" r="1.2"/><circle cx="14.5" cy="14.5" r="1.2"/></svg></div>
    <div class="benefit-text"><span>Zero benefits or payroll taxes to pay</span></div>
  </div>
  <div class="benefit" style="top:544px">
    <div class="benefit-icon"><svg width="26" height="24" viewBox="0 0 26 24" fill="none" stroke="#4b6b4d" stroke-width="1.2"><rect x="2" y="3" width="7" height="5"/><rect x="17" y="3" width="7" height="5"/><path d="M10 18l3-3 3 3v4h-6z"/><path d="M5 10c0 4 2 6 5 7M21 10c0 4-2 6-5 7M11 5h4"/></svg></div>
    <div class="benefit-text"><span>100% remote, with onsite work from time-to-time at your discretion</span></div>
  </div>
  <div class="benefit" style="top:591px">
    <div class="benefit-icon"><svg width="22" height="24" viewBox="0 0 22 24" fill="none" stroke="#4b6b4d" stroke-width="1.2"><rect x="2" y="2" width="14" height="19"/><path d="M5 12v-3M8 12v-5M11 12v-4M5 15h8M5 18h6"/><circle cx="16" cy="18" r="3.5"/></svg></div>
    <div class="benefit-text"><span>Receive LP-friendly reports to prove your differentiation and ensure their satisfaction</span></div>
  </div>

  <div class="footer footer-name">Corvath Summit, LLC</div>
  <div class="footer footer-contacts">
    <div class="contact"><svg width="7" height="9" viewBox="0 0 7 9" fill="none" stroke="#fff" stroke-width=".8"><path d="M3.5 8.5S.5 5 .5 3.3a3 3 0 016 0C6.5 5 3.5 8.5 3.5 8.5z"/><circle cx="3.5" cy="3.3" r="1"/></svg><span>48 Larkspur Lane, Unit 210,<br>Fairhaven, CT 06830 USA</span></div>
    <div class="contact"><svg width="8" height="8" viewBox="0 0 8 8" fill="none" stroke="#fff" stroke-width=".8"><path d="M1 1.5L2.5.8 3.6 2.8 2.7 3.6a4 4 0 001.7 1.7l.8-.9 2 1.1-.7 1.5C4 7 1 4 1 1.5z"/></svg><span>804.555.0187</span></div>
    <div class="contact"><svg width="8" height="8" viewBox="0 0 8 8" fill="none" stroke="#fff" stroke-width=".7"><circle cx="4" cy="4" r="3.4"/><path d="M.6 4h6.8M4 .6c1.8 2 1.8 4.8 0 6.8M4 .6c-1.8 2-1.8 4.8 0 6.8"/></svg><span>www.CorvathSummit.com<br>DeanM@CorvathSummit.com</span></div>
  </div>
</section>

<!-- BACK -->
<section class="page page--back">
  <div class="abs brand-area brand-area--back">
    <div class="brand" style="top:14px">
      <span class="brand-mark"></span>
      <div class="brand-name" style="font-size:16px">Corvath Summit</div>
      <div class="brand-sub" style="font-size:7px;letter-spacing:6px;margin-top:5px">PARTNERS</div>
    </div>
  </div>
  <div class="photo photo--ai" role="img" aria-label="Business person touching a glowing AI technology interface"></div>
  <h1 class="services-title">Our Fractional<br>Marketing Services</h1>

  <h2 class="abs mission-band">Our Mission</h2>
  <p class="abs mission-text"><b>Corvath Summit Partners</b> was created to bring <b>Fractional Marketing Services</b> to middle market investors and the <b>Intermediaries</b> and <b>Counselors</b> who serve them. For years, the <b>Fractional Marketing Services</b> concept has been leveraged in <b>Private Equity</b>, but only for <b>Portfolio Companies</b>, with little <b>Corporate Marketing</b> attention given to the funds themselves. Finally, <b>Private Equity Funds, Family Offices</b>, and <b>Investment Banks</b> are realizing they are too busy competing to win the next deal and enhancing Portco equity value to be able to focus on a <b>Marketing</b> and <b>Lead Generation</b> ecosystem that is dynamic and ever-changing. Why not leave the execution of your critical marketing function to a firm that lives and breathes <b>Private Equity, Family Office</b>, and <b>Investment Bank Marketing</b> full-time?</p>
  <p class="abs mission-contact">Contact us for a <b>no obligation</b> discussion at <b>DeanM@CorvathSummit.com</b> or <b>1.804.555.0187</b>.</p>
  <div class="rule" style="left:16px;top:286px;width:216px"></div>

  <h2 class="abs heading founder-headline">Principal<br>&amp; Founder</h2>
  <div class="photo photo--founder" role="img" aria-label="Portrait of the founder seated at his office desk"></div>
  <p class="abs founder-text founder-text--narrow">Dean Marlowe has over 25 years of <b>Private Equity</b> experience, 17 of which have been spent as Chief Marketing Officer (CMO) for middle market <b>Private</b></p>
  <p class="abs founder-text founder-text--rest"><b>Equity</b> funds. As a past <b>General Partner</b>, his knowledge of <b>Private Equity</b> marketing, business development, fundraising, principal investing, and portfolio company enhancement, positions him unlike any other in the middle market: <b><i>“A Marketer with an Investor’s Mindset,”</i></b> Dean has experience in buyouts, non-control/mezzanine, growth equity, ABL, and venture capital asset classes and brings firsthand <b>PE</b> experience and knowledge of what GPs must accomplish with their marketing efforts to satisfy their complex stakeholders.</p>

  <h2 class="abs heading quote-headline">“A Marketer With An<br>Investor’s Mindset”</h2>
  <div class="rule" style="left:16px;top:521px;width:216px"></div>
  <ul class="abs proof-list">
    <li>17-Years as a Private Equity CMO—one of the industry’s first</li>
    <li>25-Years total Private Equity experience, including Marketing, Business Development, Fundraising &amp; Principal Investing</li>
    <li>40-Years total Sales and Marketing experience, including Corporate and Global Strategy Consulting</li>
    <li>Experienced in most asset classes, including Buyouts, Non-Control/Mezzanine, Growth Equity, ABL and Venture</li>
    <li>More deal, business development, and marketing experience than any Analyst or Associate typically assigned to marketing roles</li>
    <li>Arguably, the most experienced middle market Private Equity marketer in the U.S.</li>
  </ul>

  <div class="panel panel--retained">
    <h3 class="panel-title">Monthly Retained<br>Marketing Services</h3>
    <div class="panel-rule"></div>
    <p class="panel-note">Up to 20-Hours/Month<br>Strategy, Management &amp; Execution</p>
    <ul class="panel-list">
      <li>Press Release Drafting &amp; Distribution</li>
      <li>Email Campaigns &amp; Drip Marketing / Lead Nurturing</li>
      <li>Digital Marketing &amp; Advertising</li>
      <li>Content Development &amp; Collateral Management</li>
      <li>Website Analysis, Updates &amp; Remarketing</li>
      <li>SEO &amp; SEM</li>
      <li>Dashboard &amp; KPIs</li>
      <li>Vendor Tool Selection &amp; Implementation</li>
      <li>List Management</li>
      <li>Go-to-Market Strategy</li>
      <li>ProNet Enhancement &amp; Lead Gen</li>
      <li>Other Social Media</li>
      <li>Offline Activity Management</li>
    </ul>
  </div>

  <div class="panel panel--audit">
    <h3 class="panel-title">Marketing Audit &amp;<br>Planning Services</h3>
    <div class="panel-rule"></div>
    <p class="panel-note">Assessment Areas</p>
    <ul class="panel-list">
      <li>Website &amp; Traffic Analysis</li>
      <li>SEO &amp; SEM</li>
      <li>Social Media (e.g., ProNet, etc.)</li>
      <li>Email &amp; Other Digital</li>
      <li>Press Releases</li>
      <li>Collaterals</li>
      <li>Content Management / CMS</li>
      <li>Chat Assistants and A.I.</li>
      <li>Advertising (if applicable)—all channels</li>
      <li>Full-Funnel Evaluation</li>
      <li>Biz Dev &amp; Marketing Integration</li>
      <li>CRM &amp; Data Integrity</li>
      <li>Creative Assessment</li>
      <li>Strategy, Messaging &amp; Marketing Plan (optional)</li>
    </ul>
  </div>

  <div class="panel panel--launch">
    <h3 class="panel-title">New Fund<br>Launch Services</h3>
    <div class="panel-rule" style="width:90px;margin-bottom:12px"></div>
    <ul class="panel-list" style="width:130px">
      <li>For Inaugural &amp; Follow-on Funds</li>
      <li>Can commence before or during fundraising</li>
      <li>6 &amp; 12-Month Projects</li>
      <li>Limited Availability</li>
      <li>Fees based on fund size, number, stage &amp; complexity</li>
    </ul>
    <ul class="panel-list col-right" style="top:10px">
      <li>Includes all Fractional Marketing Services (above)</li>
      <li>Plus: Website creation or overhaul</li>
      <li>Plus: CRM design &amp; implementation</li>
      <li>Plus: Corporate identity work</li>
      <li>Plus: Social media &amp; digital launch</li>
      <li>Plus: Marketing Audit for follow-on funds</li>
      <li>Plus: Business development and GTM strategy</li>
    </ul>
  </div>

  <div class="panel panel--special">
    <h3 class="panel-title">Special Projects</h3>
    <div class="panel-rule" style="width:90px;margin-bottom:8px"></div>
    <ul class="panel-list" style="width:130px">
      <li>Branding &amp; Rebranding</li>
      <li>Website Overhaul</li>
      <li>Corporate Identity</li>
      <li>Data Cleansing</li>
      <li>Video Production &amp; Management</li>
    </ul>
    <ul class="panel-list col-right" style="top:20px">
      <li>CRM Selection, Design &amp; Transition</li>
      <li>Customer Intelligence Studies</li>
      <li>Marketing Brainstorming &amp; Facilitation</li>
      <li>Marketing Resource Evaluation</li>
      <li>Boards of Directors</li>
    </ul>
  </div>

  <div class="footer footer-name" style="padding-left:16px">Corvath Summit, LLC
    <div class="footer-copy">Copyright © 2023<br>All Rights Reserved</div>
  </div>
  <div class="footer footer-contacts">
    <div class="contact"><svg width="7" height="9" viewBox="0 0 7 9" fill="none" stroke="#fff" stroke-width=".8"><path d="M3.5 8.5S.5 5 .5 3.3a3 3 0 016 0C6.5 5 3.5 8.5 3.5 8.5z"/><circle cx="3.5" cy="3.3" r="1"/></svg><span>48 Larkspur Lane, Unit 210,<br>Fairhaven, CT 06830 USA</span></div>
    <div class="contact"><svg width="8" height="8" viewBox="0 0 8 8" fill="none" stroke="#fff" stroke-width=".8"><path d="M1 1.5L2.5.8 3.6 2.8 2.7 3.6a4 4 0 001.7 1.7l.8-.9 2 1.1-.7 1.5C4 7 1 4 1 1.5z"/></svg><span>804.555.0187</span></div>
    <div class="contact"><svg width="8" height="8" viewBox="0 0 8 8" fill="none" stroke="#fff" stroke-width=".7"><circle cx="4" cy="4" r="3.4"/><path d="M.6 4h6.8M4 .6c1.8 2 1.8 4.8 0 6.8M4 .6c-1.8 2-1.8 4.8 0 6.8"/></svg><span>www.CorvathSummit.com<br>DeanM@CorvathSummit.com</span></div>
  </div>
</section>

</body>
</html>
```